Willow Crest Brand - Bag Design

We are a company dealing with nuts, grains and seeds and are looking for a design for our retail bag packaging that will be consistent across all our product range. We are currently differentiating in way of color but please feel free to be more creative if you wish. Sample of products include pumpkin seeds, rolled oats, almonds, etc.
Design Idea: Hygienic, Natural (from Nature), Quality & Upscale, Simple & Clean design
Target Market: High-end Markets, end-users of A/B type.
1. Bag size is 210 mm (width) * 310 mm (length). Material is OPP or multi-layer PP.
2. Front must have clear window to show packed products. Back clear window is optional.
3. Front side must have logo that stands out (Willow Crest) as attached.
4. Front side must have product name and net weight.
5. Back side must have enough space for Nutrition Fact, product descriptions (110 mm * 100 mm), and barcode.
6. Back side must have white space to print production and expiry dates about 25 mm * 30 mm.
7. Top and bottom of bag must be opaque and not show product.
Reason: Extended period for more new ideas and also for requested modification.
Target Market(s)
Premium market. Type A to B customers as well as professional clients. The product is not a snack. It is for cooking or baking.
Industry/Entity Type
Food Store
Requirements
Must have
- Look unique and stand out from others in the market.
- The colors of the word "Willow Crest" and the blue air-brush in the logo can be changed.
Nice to have
- See project description
Should not have
- See project description

```html
<!DOCTYPE html>
<html lang="en">
<head>
<meta charset="utf-8">
<title>Willow Crest – Pumpkin Seeds Bag Front</title>
<link href="https://fonts.googleapis.com/css2?family=Oswald:wght@400;500&family=Lato:wght@400&display=swap" rel="stylesheet">
<style>
  :root {
    --bag-white: #f9f9f9;
    --bag-edge: #ececec;
    --brand-red: #c21f35;
    --brand-yellow: #f2c500;
    --leaf-green: #1f9a3e;
    --badge-green: #b9d334;
    --badge-ink: #1e1e1e;
    --seed-light: #efe6d2;
    --seed-deep: #d6c8a8;
    --ink-grey: #555555;
  }
  * { margin: 0; padding: 0; box-sizing: border-box; }
  html, body {
    width: 960px;
    height: 1200px;
    overflow: hidden;
    background: var(--bag-white);
  }
  .bag-front {
    position: relative;
    width: 960px;
    height: 1200px;
    background: linear-gradient(180deg, var(--bag-edge) 0, var(--bag-white) 40px, var(--bag-white) 100%);
    font-family: "Lato", sans-serif;
  }
  .brand {
    position: absolute;
    left: 130px;
    top: 190px;
    display: flex;
    align-items: center;
    gap: 30px;
  }
  .brand-dot {
    flex: none;
    width: 150px;
    height: 150px;
    border-radius: 50%;
    background: var(--brand-yellow);
  }
  .brand-name {
    font-family: "Oswald", sans-serif;
    font-weight: 500;
    font-size: 104px;
    line-height: 1.08;
    color: var(--brand-red);
    letter-spacing: 1px;
  }
  .product-name {
    position: absolute;
    left: 97px;
    top: 470px;
    font-family: "Oswald", sans-serif;
    font-weight: 400;
    font-size: 100px;
    line-height: 96px;
    color: var(--leaf-green);
  }
  .net-weight {
    position: absolute;
    left: 110px;
    top: 984px;
    font-size: 21px;
    color: var(--ink-grey);
  }
  .product-window {
    position: absolute;
    left: 376px;
    top: 488px;
    width: 530px;
    height: 530px;
  }
  .natural-badge {
    position: absolute;
    left: 694px;
    top: 912px;
    width: 176px;
    height: 176px;
    border-radius: 50%;
    background: var(--badge-green);
    display: flex;
    flex-direction: column;
    align-items: center;
    justify-content: center;
    font-family: "Oswald", sans-serif;
    font-weight: 500;
    color: var(--badge-ink);
    text-align: center;
  }
  .natural-badge .badge-figure {
    font-size: 44px;
    line-height: 1;
  }
  .natural-badge .badge-word {
    font-size: 40px;
    line-height: 1.05;
  }
  .base-band {
    position: absolute;
    left: 0;
    bottom: 14px;
    width: 100%;
    height: 16px;
    background: var(--leaf-green);
  }
</style>
</head>
<body>
  <main class="bag-front">
    <div class="brand">
      <span class="brand-dot"></span>
      <span class="brand-name">Willow<br>Crest</span>
    </div>

    <h1 class="product-name">Pumpkin<br>Seeds</h1>

    <svg class="product-window" viewBox="0 0 530 530">
      <defs>
        <radialGradient id="seedFill" cx="50%" cy="45%" r="55%">
          <stop offset="0%" stop-color="var(--seed-light)"/>
          <stop offset="100%" stop-color="var(--seed-deep)"/>
        </radialGradient>
      </defs>
      <circle cx="265" cy="265" r="238" fill="none" stroke="var(--brand-red)" stroke-width="40"/>
      <circle cx="265" cy="265" r="215" fill="url(#seedFill)" role="img" aria-label="Clear window showing the packed white pumpkin seeds"/>
    </svg>

    <div class="natural-badge">
      <span class="badge-figure">100%</span>
      <span class="badge-word">natural</span>
    </div>

    <p class="net-weight">Net Wt. 16 OZ (454g)</p>

    <div class="base-band"></div>
  </main>
</body>
</html>
```